Verlindo Magician

I want the business card for my business to give to people who watch that later I will be employed to show magic here is my website http://www.verlindoillusions.example/I want the interesting design , i am very opened for formal and informal, I watch a lot of design so don't stick to the common shape and form but i hope it can also be produced the thing to write on will be the same as in picture that i will upload , i also will upload the logo for you that so can be easy to useDenis CostilleMagicianMAGICIAN VERLINDO 17 rue des Tilleuls - 25000 BESANÇON contact@verlindoillusions.example tel. 0381 946 157 tel. 0674 219 503

```html
<!DOCTYPE html>
<html lang="fr">
<head>
<meta charset="utf-8">
<title>Verlindo Magician – Business Card</title>
<link rel="stylesheet" href="https://fonts.googleapis.com/css2?family=Jost:wght@400&family=Open+Sans:wght@400;700&display=swap">
<style>
  :root {
    --backdrop: #353535;
    --card: #ffffff;
    --ink: #111111;
    --accent: #d9382b;
    --rule: #bdbdbd;
    --portrait-dark: #1a1a1a;
    --portrait-light: #5a5a5a;
  }
  * { margin: 0; padding: 0; box-sizing: border-box; }
  html, body { width: 1200px; height: 900px; overflow: hidden; }
  body {
    background: var(--backdrop);
    position: relative;
    font-family: "Open Sans", Arial, sans-serif;
    color: var(--ink);
  }
  .card {
    position: absolute;
    top: 275px;
    width: 477px;
    height: 293px;
    background: var(--card);
  }
  .card--front { left: 120px; border-radius: 0 46px 0 46px; }
  .card--back { left: 606px; border-radius: 46px 0 46px 0; }

  .portrait {
    position: absolute;
    background: linear-gradient(180deg, var(--portrait-light), var(--portrait-dark));
    border-radius: 40px 40px 12px 12px;
  }
  .card--front .portrait { left: 40px; top: 48px; width: 127px; height: 160px; }
  .card--back .portrait { left: 170px; top: 32px; width: 140px; height: 176px; }

  .brand-name {
    position: absolute;
    font-family: "Jost", "Futura", sans-serif;
    font-weight: 400;
    color: var(--ink);
    letter-spacing: 1px;
    text-align: center;
    line-height: 1;
  }
  .card--front .brand-name { left: 20px; width: 165px; top: 210px; font-size: 25px; }
  .card--back .brand-name { left: 140px; width: 200px; top: 209px; font-size: 29px; }

  .divider {
    position: absolute;
    left: 195px; top: 62px;
    width: 1px; height: 170px;
    background: var(--rule);
  }
  .details { position: absolute; left: 219px; top: 60px; }
  .holder-name { font-size: 18px; font-weight: 700; line-height: 20px; letter-spacing: .2px; }
  .holder-role { font-size: 13px; color: var(--accent); line-height: 17px; margin-bottom: 6px; }
  .contact-list { list-style: none; }
  .contact-list li {
    font-size: 14px; line-height: 17.5px;
    display: flex; align-items: center; gap: 4px;
  }
  .contact-list svg { width: 12px; height: 12px; fill: var(--ink); flex: none; }
  .business { margin-top: 7px; font-size: 14px; line-height: 17px; }
  .business-name { font-weight: 700; }
</style>
</head>
<body>
  <section class="card card--front" aria-label="Business card front">
    <div class="portrait" role="img" aria-label="Black and white illustrated portrait of the magician holding a playing card"></div>
    <div class="brand-name">VERLINDO</div>
    <div class="divider"></div>
    <div class="details">
      <p class="holder-name">MARC RAVOULET</p>
      <p class="holder-role">Magician</p>
      <ul class="contact-list">
        <li><svg viewBox="0 0 12 12" aria-hidden="true"><path d="M1 4c0-2 2-3 5-3s5 1 5 3v1H8V4H4v1H1z M2 6h8l1 5H1z"/></svg>0381 946 157</li>
        <li><svg viewBox="0 0 12 12" aria-hidden="true"><path d="M1 4c0-2 2-3 5-3s5 1 5 3v1H8V4H4v1H1z M2 6h8l1 5H1z"/></svg>0674 219 503</li>
        <li><svg viewBox="0 0 12 12" aria-hidden="true"><path d="M1 3h10v7H1z" fill="none" stroke="#111" stroke-width="1.3"/><path d="M1 3l5 4 5-4" fill="none" stroke="#111" stroke-width="1.3"/></svg>contact@verlindoillusions.example</li>
        <li><svg viewBox="0 0 12 12" aria-hidden="true"><circle cx="6" cy="6" r="5.5"/><path d="M3 4h3l1 2-2 1-1 3-1-2z M8 3l2 2-1 2z" fill="#fff"/></svg>www.verlindoillusions.example</li>
      </ul>
      <div class="business">
        <p class="business-name">MAGICIAN VERLINDO</p>
        <p>17 rue des Tilleuls - 25000</p>
        <p>BESANÇON</p>
      </div>
    </div>
  </section>

  <section class="card card--back" aria-label="Business card back">
    <div class="portrait" role="img" aria-label="Black and white illustrated portrait of the magician holding a playing card"></div>
    <div class="brand-name">VERLINDO</div>
  </section>
</body>
</html>
```